TEBSIRK HOA Portal Site for Public

Clean up and organize current website; need website to look good and functional; this is a HOA (homeowner association management) website where homeowners can login and pay their bill, general information about a HOA, monthly newsletter page.
Competitors:
https://quillmarsh.example/
https://dorvinpalms.example/
https://www.kelbrookhomes.example/nevada
http://www.tpw-hoa.example/

Target Market(s)

homeowners

Industry/Entity Type

Real Estate

Coding

Coded - Design and coding required

Number of Pages Required

5+ page

Font styles to use
Serif

Colors
0292cd
33a6d7
e667a6
e34297

Requirements
Must have
• login to pay
• services page
• contact us
• order resale package
Nice to have
• page why an HOA would contract us

```html
<!DOCTYPE html>
<html lang="en">
<head>
<meta charset="utf-8">
<title>TEBSIRK HOA – Homeowner Association Management</title>
<link href="https://fonts.googleapis.com/css2?family=Roboto:wght@500;700&family=Lato:wght@400;700&display=swap" rel="stylesheet">
<style>
:root{
  --blue:#0292cd;
  --blue-light:#33a6d7;
  --pink:#e34297;
  --pink-soft:#e667a6;
  --ink:#111;
  --text:#555;
  --grey-band:#efefef;
  --footer-bg:#e6f3fa;
  --line:#d9d9d9;
}
*{box-sizing:border-box;margin:0;padding:0}
html,body{width:1200px;height:3781px;overflow:hidden}
body{position:relative;background:#fff;font-family:'Lato',sans-serif;color:var(--text)}
.abs{position:absolute}
.heading{font-family:'Roboto',sans-serif;font-weight:700;color:var(--blue);font-size:38px;line-height:1.1}
.center{left:0;width:1200px;text-align:center}
.divider{position:absolute;height:2px;width:90px;background:var(--pink)}
.divider::after{content:"";position:absolute;left:50%;top:-4px;width:10px;height:10px;margin-left:-5px;border:2px solid var(--pink);border-radius:50%;background:#fff}
.btn{position:absolute;background:var(--pink);color:#fff;font-family:'Roboto',sans-serif;font-weight:700;font-size:16px;display:flex;align-items:center;justify-content:center}
.btn::before{content:"";position:absolute;left:0;top:-9px;width:40px;height:2px;background:var(--pink)}
.btn::after{content:"";position:absolute;right:0;bottom:-9px;width:40px;height:2px;background:var(--pink)}
.photo{position:absolute}
.body-text{font-size:12px;line-height:19.5px;color:var(--text)}

/* nav */
.nav-logo{left:163px;top:16px;font-family:'Roboto',sans-serif;font-weight:700;font-size:22px;color:var(--blue)}
.nav-links{left:518px;top:22px;display:flex;gap:26px;font-size:12px;color:var(--ink)}
.nav-links .active{font-weight:700}
.login{left:956px;top:12px;width:83px;height:37px;font-size:15px}
.login::before,.login::after{display:none}

/* hero */
.hero{left:0;top:59px;width:1200px;height:601px;background:linear-gradient(180deg,#8da7d8 0%,#c7b0d0 35%,#5e6f94 60%,#3a3f55 100%)}
.hero-overlay{left:0;top:59px;width:525px;height:601px;background:linear-gradient(180deg,rgba(2,146,205,.92),rgba(20,110,160,.9))}
.hero-frame{left:161px;top:135px;width:450px;height:449px;border:8px solid rgba(255,255,255,.55)}
.hero-kicker{left:192px;top:202px;font-family:'Roboto',sans-serif;font-weight:700;font-size:15px;color:#111;display:flex;align-items:center;gap:10px}
.hero-kicker::before{content:"";width:59px;height:1px;background:#111}
.hero-title{left:193px;top:245px;font-family:'Roboto',sans-serif;font-weight:700;font-size:45px;line-height:52px;color:#fff}
.hero-btn{left:191px;top:459px;width:135px;height:44px;font-size:18px}

/* services */
.card{position:absolute;top:814px;width:427px;height:343px;background:#fff;box-shadow:0 2px 10px rgba(0,0,0,.15)}
.card .photo{left:0;top:0;width:427px;height:261px}
.card-icon{position:absolute;left:0;top:261px;width:82px;height:82px;background:var(--blue);display:flex;align-items:center;justify-content:center}
.card-title{position:absolute;left:95px;top:272px;font-family:'Roboto',sans-serif;font-weight:700;font-size:13px;color:var(--ink)}
.card-text{position:absolute;left:95px;top:293px;width:300px;font-size:11.5px;line-height:19px;color:var(--text)}
.card-read{left:157px;top:110px;width:113px;height:37px;font-size:15px}
.card-read::before,.card-read::after{display:none}

/* offer */
.offer-band{left:0;top:1278px;width:1200px;height:434px;background:var(--grey-band)}
.offer-list{left:163px;top:1414px;width:430px}
</style>
</head>
<body>

<!-- Navigation -->
<header>
  <div class="abs nav-logo">TEBSIRK HOA</div>
  <nav class="abs nav-links">
    <span>Home</span><span class="active">About Us</span><span>Services</span><span>Why Us</span><span>Contact Us</span>
  </nav>
  <a class="btn login">Login</a>
</header>

<!-- Hero -->
<section>
  <div class="abs hero" role="img" aria-label="Photo of a two-storey suburban house at dusk with lit windows"></div>
  <div class="abs hero-overlay"></div>
  <div class="abs hero-frame"></div>
  <div class="abs hero-kicker">TEBSIRK HOA</div>
  <h1 class="abs hero-title">HOMEOWNER<br>ASSOCIATION<br>MANAGEMENT</h1>
  <a class="btn hero-btn">Contact Us</a>
</section>

<!-- Services -->
<section>
  <h2 class="abs heading center" style="top:720px">Our Services</h2>
  <div class="divider" style="left:555px;top:770px"></div>

  <article class="card" style="left:161px">
    <div class="photo" style="background:linear-gradient(180deg,#2a3345,#1f2430)" role="img" aria-label="Photo of a row of Victorian houses at night"></div>
    <a class="btn card-read">Read More</a>
    <div class="card-icon">
      <svg width="48" height="46" viewBox="0 0 48 46" fill="none" stroke="#fff" stroke-width="3" stroke-linejoin="round"><path d="M4 22 24 4l20 18"/><path d="M9 18v24h30V18"/><path d="M20 42V29h8v13"/></svg>
    </div>
    <h3 class="card-title">Homeowner Association Management Services</h3>
    <p class="card-text">Lorem Ipsum is simply dummy text of the printing and typesetting industry.</p>
  </article>

  <article class="card" style="left:612px">
    <div class="photo" style="background:linear-gradient(180deg,#6d8f6a 0%,#9aa3ab 45%,#6f8a4e 100%)" role="img" aria-label="Photo of a grey two-storey house with a green lawn"></div>
    <div class="card-icon">
      <svg width="50" height="46" viewBox="0 0 50 46" fill="none" stroke="#fff" stroke-width="3"><path d="M4 44V4h24v40M28 18h18v26M2 44h46"/><path d="M10 12h4M18 12h4M10 20h4M18 20h4M10 28h4M18 28h4M34 26h4M34 34h4"/></svg>
    </div>
    <h3 class="card-title">Homeowner Association Management Services</h3>
    <p class="card-text">Lorem Ipsum is simply dummy text of the printing and typesetting industry.</p>
  </article>
</section>

<!-- What we offer -->
<section>
  <div class="abs offer-band"></div>
  <div class="photo" style="left:701px;top:1226px;width:427px;height:300px;background:linear-gradient(180deg,#d7d0c4 0%,#a3876f 55%,#7f9a58 100%)" role="img" aria-label="Photo of a smiling couple standing in front of their home"></div>
  <div class="photo" style="left:559px;top:1574px;width:352px;height:186px;background:linear-gradient(180deg,#6a8aa3 0%,#8b7562 50%,#4a5a3a 100%)" role="img" aria-label="Photo of a brick house with a pickup truck in the driveway"></div>
  <h2 class="abs heading" style="left:163px;top:1338px">What We Offer</h2>
  <div class="divider" style="left:163px;top:1390px"></div>
  <p class="abs body-text offer-list">Accessible, licensed Association Managers<br>24 hour Web site access: online account information<br>24 hour emergency service<br>Provide monthly financial reports to the Board of Directors<br>Read, study and understand all governing documents of the Association.<br>Correspond with members in violation of the CC&amp;Rs, By-laws, Rules &amp; Regulations and report the status of all noncompliance to the Board of Directors in a timely manner.</p>
  <a class="btn" style="left:161px;top:1612px;width:113px;height:38px;font-size:15px">Read More</a>
</section>

<!-- About -->
<section>
  <h2 class="abs heading center" style="top:1818px">About Us</h2>
  <div class="divider" style="left:555px;top:1868px"></div>
  <p class="abs body-text" style="left:300px;top:1902px;width:600px;text-align:center">Lorem Ipsum is simply dummy text of the printing and typesetting industry. Lorem Ipsum has been the industry's standard dummy text ever since the 1500s, when an unknown printer took a galley of type and scrambled it to make a type specimen book.<br><br>It has survived not only five centuries, but also the leap into electronic typesetting, remaining essentially unchanged.</p>
  <a class="btn" style="left:543px;top:2054px;width:113px;height:38px;font-size:15px">Get Started</a>
</section>

<!-- Why us -->
<section>
  <div class="abs" style="left:0;top:2183px;width:431px;height:337px;border:9px solid var(--pink);border-left:none"></div>
  <div class="photo" style="left:25px;top:2220px;width:535px;height:262px;background:linear-gradient(90deg,#d9e3ea 0%,#a8b9c8 40%,#3d5f8a 60%,#c9d4dc 100%)" role="img" aria-label="Photo of a couple embracing in front of a modern white house"></div>
  <h2 class="abs heading" style="left:613px;top:2172px;line-height:39px">Why an HOA would<br>Contract Us</h2>
  <p class="abs body-text" style="left:613px;top:2280px;width:420px">Lorem Ipsum is simply dummy text of the printing and typesetting industry. Lorem Ipsum has been the industry's standard dummy text ever since the 1500s, when an unknown printer took a galley of type and scrambled it to make a type specimen book.<br><br>It has survived not only five centuries, but also the leap into electronic typesetting, remaining essentially unchanged.</p>
  <a class="btn" style="left:612px;top:2482px;width:111px;height:37px;font-size:15px">Read More</a>
</section>

<!-- Testimonials -->
<section>
  <h2 class="abs heading center" style="top:2598px">Our Testimonials</h2>
  <div class="divider" style="left:555px;top:2648px"></div>
  <div class="photo" style="left:165px;top:2728px;width:96px;height:96px;border-radius:50%;background:#3a3a3a" role="img" aria-label="Portrait photo of a client"></div>
  <div class="photo" style="left:303px;top:2701px;width:60px;height:60px;border-radius:50%;background:#6b5a4d" role="img" aria-label="Portrait photo of a client"></div>
  <div class="photo" style="left:264px;top:2821px;width:76px;height:76px;border-radius:50%;background:#8a8f96" role="img" aria-label="Portrait photo of a client"></div>
  <div class="abs" style="left:376px;top:2708px;width:487px;height:186px;border:1px solid var(--blue-light);border-radius:4px;padding:28px 24px 0">
    <p style="font-weight:700;font-size:13px;color:var(--ink)">Lorem Ipsum is simply dummy text of the printing and typesetting.</p>
    <p class="body-text" style="margin-top:6px">Lorem Ipsum is simply dummy text of the printing and typesetting industry. Lorem Ipsum has been the industry's standard dummy text ever since the 1500s, when an unknown printer took a galley of type and scrambled it to make a type specimen book.</p>
    <p style="margin-top:12px;font-family:'Roboto',sans-serif;font-weight:700;font-size:11px;color:var(--blue)">- CLIENT NAME</p>
  </div>
  <svg class="abs" style="left:843px;top:2764px" width="37" height="74" viewBox="0 0 37 74" fill="#fff" stroke="#33a6d7" stroke-width="1.5"><rect x=".75" y=".75" width="35.5" height="35.5"/><rect x=".75" y="37.75" width="35.5" height="35.5"/><path d="M21 12l-6 6 6 6M16 49l6 6-6 6" fill="none" stroke-width="2"/></svg>
  <div class="abs" style="left:161px;top:2943px;width:878px;height:1px;background:var(--line)"></div>
</section>

<!-- Contact form -->
<section>
  <h2 class="abs heading center" style="top:2988px">Get In Touch</h2>
  <div class="divider" style="left:555px;top:3040px"></div>
  <div class="abs" style="left:311px;top:3075px;width:282px;height:44px;border:1px solid var(--line);padding:14px 12px;font-size:12px">Name:</div>
  <div class="abs" style="left:607px;top:3075px;width:282px;height:44px;border:1px solid var(--line);padding:14px 12px;font-size:12px">Email:</div>
  <div class="abs" style="left:311px;top:3135px;width:282px;height:44px;border:1px solid var(--line);padding:14px 12px;font-size:12px">Phone:</div>
  <div class="abs" style="left:607px;top:3135px;width:282px;height:44px;border:1px solid var(--line);padding:14px 12px;font-size:12px">Subject:</div>
  <div class="abs" style="left:311px;top:3195px;width:578px;height:88px;border:1px solid var(--line);padding:14px 12px;font-size:12px">Message:</div>
  <a class="btn" style="left:543px;top:3337px;width:113px;height:37px;font-size:15px">Submit</a>
</section>

<!-- Footer -->
<footer>
  <div class="abs" style="left:0;top:3442px;width:1200px;height:339px;background:var(--footer-bg)"></div>
  <div class="abs" style="left:163px;top:3490px;font-family:'Roboto',sans-serif;font-weight:700;font-size:22px;color:var(--blue)">TEBSIRK HOA</div>
  <p class="abs" style="left:163px;top:3537px;width:210px;font-size:11px;line-height:18px">Lorem Ipsum is simply dummy text of the printing and typesetting industry. Lorem Ipsum has been the industry's.</p>
  <svg class="abs" style="left:161px;top:3612px" width="170" height="34" viewBox="0 0 170 34" fill="none" stroke="#e34297" stroke-width="1.5"><circle cx="17" cy="17" r="15.5"/><circle cx="62" cy="17" r="15.5"/><circle cx="107" cy="17" r="15.5"/><circle cx="152" cy="17" r="15.5"/></svg>

  <h4 class="abs" style="left:387px;top:3494px;font-size:14px;font-weight:400;color:var(--pink)">Quick Link</h4>
  <ul class="abs" style="left:387px;top:3533px;list-style:none;font-size:11.5px;line-height:24px">
    <li>▸ &nbsp;Home</li><li>▸ &nbsp;About Us</li><li>▸ &nbsp;Services</li><li>▸ &nbsp;Why Us</li><li>▸ &nbsp;Contact Us</li>
  </ul>

  <h4 class="abs" style="left:613px;top:3494px;font-size:14px;font-weight:400;color:var(--pink)">Contact Info</h4>
  <svg class="abs" style="left:611px;top:3535px" width="16" height="100" viewBox="0 0 16 100" fill="none" stroke="#e34297" stroke-width="1.4"><path d="M3 2c2 0 3 3 2 4l-1 1c1 2 3 4 5 5l1-1c1-1 4 0 4 2s-2 3-3 3C6 16 0 10 0 5c0-1 1-3 3-3z"/><rect x="1" y="41" width="14" height="10"/><path d="M1 41l7 6 7-6"/><path d="M8 96c4-5 6-8 6-11a6 6 0 0 0-12 0c0 3 2 6 6 11z"/><circle cx="8" cy="85" r="2"/></svg>
  <p class="abs" style="left:643px;top:3533px;font-size:11.5px">+91-000-000-0000</p>
  <p class="abs" style="left:643px;top:3571px;font-size:11.5px">info@tebsirkhoa.example</p>
  <p class="abs" style="left:643px;top:3609px;width:160px;font-size:11.5px;line-height:19px">100- Lorem ipsum is simply dummy text.</p>

  <h4 class="abs" style="left:838px;top:3494px;font-size:14px;font-weight:400;color:var(--pink)">Newsletter</h4>
  <p class="abs" style="left:838px;top:3533px;width:205px;font-size:11px;line-height:18px"><b style="color:var(--blue)">SIGN UP FOR OUR NEWSLETTER –</b><br>Stay current with our news and insight</p>
  <div class="abs" style="left:837px;top:3600px;width:202px;height:36px;border:1px solid #b9c6cf;background:#fff;padding:11px 12px;font-size:11px">Enter Email:</div>
  <a class="btn" style="left:837px;top:3663px;width:113px;height:37px;font-size:14px">Subscribe Us</a>

  <div class="abs" style="left:161px;top:3719px;width:878px;height:1px;background:var(--pink)"></div>
  <p class="abs center" style="top:3741px;font-size:11.5px;color:#222">Copyright © -2019 <span style="color:var(--blue)">TEBSIRK HOA</span>. All Right Reserved, &nbsp;Terms &amp; Conditions | Privacy Policy.</p>
</footer>

</body>
</html>
```